Corvana Tongue Works, LLC

We need a business card that includes information about our business and conveys a reliable business that provides document translation services and interpreters for a variety of corporate and individual clients. We want to come across as professional, reliable, yet approachable. It should include the following on one side:

ESL / ENL Language Classes, Private Lessons, and Online Tutors
PLEXA Training and Testing
Translating & Interpreting Services
Contact us about Over-the-Phone Interpreting in over 200 languages
24/7/365
www.corvanatongue.example

The other side should include (555) 481-3062

Rhoda Pelling, President
482 Garnet Ave., Ste. 219
Indianapolis, IN 40917

Please add USA as part of the address. Also, please add rmpelling@corvanatongueworks.example as the e-mail address. Thank you.

Target Market(s)

Business professionals, their families, the international community

Industry/Entity Type

Business

Contact Information for Business Card

24/7/365
www.corvanatongue.example

(555) 481-3062

Rhoda Pelling, President
482 Garnet Ave., Ste. 219
Indianapolis, IN 40917
USA

Font styles to use
Sans Serif

Colors

Designer to choose colors to be used in the design.

Requirements
Must have
• See project description
• e-mail address and web address
• Phone number
Nice to have
• a globe
• physical address
Should not have
• Should not have the same color scheme as other agencies in our market in Indiana unless it is blue and black. No purple or yellow.

```html
<!DOCTYPE html>
<html lang="en">
<head>
<meta charset="utf-8">
<title>Corvana Tongue Works – Business Card</title>
<link rel="stylesheet" href="https://fonts.googleapis.com/css2?family=Roboto:wght@400;500;700&family=Roboto+Condensed:wght@400;700&display=swap">
<style>
  :root {
    --backdrop: #d9d9d9;
    --card: #0b0b0c;
    --card-edge: #1b1b1d;
    --blue: #3aa3e3;
    --white: #f4f4f4;
    --muted: #cfd3d6;
  }
  * { box-sizing: border-box; margin: 0; padding: 0; }
  html, body { width: 1200px; height: 896px; overflow: hidden; }
  body {
    background: var(--backdrop);
    font-family: "Roboto", Arial, sans-serif;
    display: flex;
    align-items: center;
    justify-content: center;
    gap: 40px;
  }
  .card {
    width: 540px;
    height: 309px;
    background: linear-gradient(135deg, var(--card-edge), var(--card) 55%);
    border-radius: 18px;
    color: var(--white);
    position: relative;
    overflow: hidden;
    box-shadow: 0 10px 30px rgba(0,0,0,.35);
  }

  /* brand lockup */
  .brand { display: flex; align-items: center; gap: 12px; }
  .brand-dot {
    width: 64px; height: 64px; border-radius: 50%;
    background: var(--blue); flex: none;
  }
  .brand-name {
    font-family: "Roboto", Arial, sans-serif;
    font-weight: 500;
    color: var(--white);
    font-size: 24px;
    line-height: 1.05;
  }

  /* services side */
  .card-services { padding: 22px 30px; text-align: center; }
  .card-services .brand { justify-content: center; margin-bottom: 16px; }
  .services-list { font-size: 14px; line-height: 1.45; font-weight: 500; }
  .divider-h { height: 1px; background: var(--blue); margin: 12px 0 10px; }
  .otp { font-size: 14px; font-weight: 700; line-height: 1.45; }
  .services-web { font-size: 14px; font-weight: 500; margin-top: 6px; }

  /* contact side */
  .card-contact { display: flex; align-items: center; padding: 0 22px 0 26px; }
  .card-contact .brand { width: 176px; flex: none; gap: 10px; }
  .card-contact .brand-dot { width: 64px; height: 64px; }
  .card-contact .brand-name { font-size: 21px; }
  .divider-v { width: 1px; height: 170px; background: var(--blue); margin: 0 18px 0 4px; flex: none; }
  .contact-info { min-width: 0; }
  .contact-name {
    font-family: "Roboto Condensed", Arial, sans-serif;
    font-weight: 700; font-size: 26px; color: var(--blue);
    text-transform: uppercase; letter-spacing: .3px;
  }
  .contact-title { font-size: 13px; color: var(--muted); margin: 2px 0 10px; }
  .contact-address { font-size: 13px; line-height: 1.45; margin-bottom: 8px; }
  .contact-list { list-style: none; font-size: 12.5px; line-height: 1.6; }
  .contact-list li { display: flex; align-items: center; gap: 6px; white-space: nowrap; }
  .contact-list svg { width: 11px; height: 11px; flex: none; }
  .accent { color: var(--blue); }
</style>
</head>
<body>

  <section class="card card-services">
    <div class="brand">
      <span class="brand-dot"></span>
      <span class="brand-name">Corvana<br>Tongue Works, LLC</span>
    </div>
    <p class="services-list">
      ESL / ENL Language Classes, Private Lessons, and Online Tutors<br>
      PLEXA Training and Testing<br>
      Translating &amp; Interpreting Services
    </p>
    <div class="divider-h"></div>
    <p class="otp">
      Contact us about Over-the-Phone Interpreting in over 200 languages<br>
      24/7/365
    </p>
    <p class="services-web">www.<span class="accent">corvanatongue</span>.example</p>
  </section>

  <section class="card card-contact">
    <div class="brand">
      <span class="brand-dot"></span>
      <span class="brand-name">Corvana<br>Tongue<br>Works, LLC</span>
    </div>
    <div class="divider-v"></div>
    <div class="contact-info">
      <h1 class="contact-name">Rhoda Pelling</h1>
      <p class="contact-title">President</p>
      <p class="contact-address">482 Garnet Ave., Ste. 219<br>Indianapolis, IN 40917 USA</p>
      <ul class="contact-list">
        <li>
          <svg viewBox="0 0 12 12"><path d="M3 1l2 2.5-1.2 1.3a7 7 0 003.4 3.4L8.5 7 11 9l-1 2C5.5 11 1 6.5 1 2z" fill="var(--blue)"/></svg>
          (555) 481-3062
        </li>
        <li>
          <svg viewBox="0 0 12 12"><rect x="1" y="2.5" width="10" height="7" rx="1" fill="none" stroke="var(--blue)" stroke-width="1.2"/><path d="M1.5 3l4.5 3.5L10.5 3" fill="none" stroke="var(--blue)" stroke-width="1.2"/></svg>
          rmpelling@corvanatongueworks.example
        </li>
      </ul>
    </div>
  </section>

</body>
</html>
```